Profesional personal website needs design and business card

I need a business card with my professional name as a logo "Dorian Vitality" for my business. I am a Wellness Coach, consultant and trainer. So it should be professional, wellness oriented and modern.

Target Market(s)

Private clients, governments, corporations. Luxury and high market.

Industry/Entity Type

Health And Wellness

Contact Information for Business Card

Dorian Vitality should be the logo

Colors

Designer to choose colors to be used in the design.

Requirements
Must have
• Dorian Vitality
• Name: Tomás Lirandel
• Wellness Coach, Consultant & Trainer.
• Website: www.dorianvitality-example.com
• Phone:
• Spain (+34) 612 480 317
• (USA) +1 (555) 610 4829
Nice to have
• The most important is the design of "Dorian Vitality", as this is going to be my personal brand logo. It should be professional, wellness, high end and actual.
Should not have
• no golds, no baroque style..

```html
<!DOCTYPE html>
<html lang="en">
<head>
<meta charset="utf-8">
<title>Dorian Vitality – Business Card</title>
<link href="https://fonts.googleapis.com/css2?family=Montserrat:wght@400;500;600&display=swap" rel="stylesheet">
<style>
  :root {
    --green: #4a7c3a;
    --grey: #8a8a8a;
    --text-grey: #555555;
    --white: #ffffff;
    --backdrop: #dcd9d5;
  }
  * { margin: 0; padding: 0; box-sizing: border-box; }
  html, body {
    width: 1200px; height: 900px; overflow: hidden;
    background: var(--backdrop);
    font-family: "Montserrat", sans-serif;
  }
  .stage {
    width: 1200px; height: 900px;
    display: flex; flex-direction: column; align-items: center; justify-content: center;
    gap: 52px;
  }
  .card {
    position: relative;
    width: 620px; height: 354px;
    border-radius: 22px;
    overflow: hidden;
    box-shadow: 0 6px 18px rgba(0,0,0,0.18);
  }
  /* Front */
  .card--front {
    background: var(--green);
    color: var(--white);
    display: flex; flex-direction: column; align-items: center; justify-content: center;
  }
  .brand {
    display: flex; align-items: center; gap: 16px;
  }
  .brand__dot {
    width: 54px; height: 54px; border-radius: 50%;
    border: 3px solid currentColor;
  }
  .brand__name {
    font-weight: 600;
    font-size: 40px;
    letter-spacing: 1px;
    text-transform: uppercase;
  }
  .front__web {
    margin-top: 26px;
    font-size: 14px;
    letter-spacing: 4px;
    font-weight: 400;
  }
  /* Back */
  .card--back {
    background: var(--white);
  }
  .back__brand {
    position: absolute; top: 48px; right: 40px;
    color: var(--green);
  }
  .back__brand .brand__dot { width: 36px; height: 36px; border-width: 2px; }
  .back__brand .brand__name { font-size: 26px; }
  .contact {
    position: absolute; left: 40px; bottom: 50px;
  }
  .contact__name {
    color: var(--green);
    font-size: 25px; font-weight: 500;
    text-transform: uppercase; letter-spacing: 0.5px;
  }
  .contact__role {
    color: var(--text-grey);
    font-size: 13px; margin-bottom: 16px;
  }
  .contact__list { list-style: none; }
  .contact__list li {
    color: var(--text-grey);
    font-size: 14px; line-height: 1.55;
  }
  .contact__label {
    color: var(--green); font-weight: 600;
    display: inline-block; width: 34px;
  }
  .stripe {
    position: absolute; left: 0; right: 0; bottom: 0; height: 10px;
    display: flex;
  }
  .stripe span { flex: 1; }
  .stripe .s-green { background: var(--green); }
  .stripe .s-grey { background: var(--grey); }
</style>
</head>
<body>
<main class="stage">
  <section class="card card--front">
    <div class="brand">
      <span class="brand__dot"></span>
      <span class="brand__name">Dorian Vitality</span>
    </div>
    <p class="front__web">www.dorianvitality-example.com</p>
  </section>

  <section class="card card--back">
    <div class="brand back__brand">
      <span class="brand__dot"></span>
      <span class="brand__name">Dorian Vitality</span>
    </div>
    <div class="contact">
      <h1 class="contact__name">Tomás Lirandel</h1>
      <p class="contact__role">Wellness Coach, Consultant &amp; Trainer</p>
      <ul class="contact__list">
        <li><span class="contact__label">P :</span>(+34) 612 480 317 (Spain)</li>
        <li><span class="contact__label">P :</span>+1 (555) 610 4829 (USA)</li>
        <li><span class="contact__label">E :</span>info@dorianvitality-example.com</li>
        <li><span class="contact__label">W :</span>www.dorianvitality-example.com</li>
      </ul>
    </div>
    <div class="stripe">
      <span class="s-green"></span><span class="s-grey"></span><span class="s-green"></span><span class="s-grey"></span>
    </div>
  </section>
</main>
</body>
</html>
```